Simple and Clean business card design

We would like the design to be simple clean and to incorporate our colors.

We are open to your design and talent, we have the dots in our logo as we think of it as data points and we connect data points for people.

We are open to see the great creative and clean design you bring to the table

Contact Information for Business Card

please include: name, position, email, phone and website

Font styles to use
Sans Serif

Requirements
Must have
• my colors incorporated, simplicity
Nice to have
• lots of white space, simplicity
Should not have
• complexicity/ complex art

```html
<!DOCTYPE html>
<html lang="en">
<head>
<meta charset="utf-8">
<title>Nectra Business Card</title>
<link rel="stylesheet" href="https://fonts.googleapis.com/css2?family=Montserrat:wght@400;500;700&display=swap">
<style>
  :root {
    --stage: #2b2b2b;
    --brand-blue: #537bbf;
    --brand-green: #34a853;
    --ink: #111111;
    --paper: #ffffff;
    --rule: #9a9a9a;
  }
  * { margin: 0; padding: 0; box-sizing: border-box; }
  html, body {
    width: 1200px; height: 900px; overflow: hidden;
    background: var(--stage);
    font-family: "Montserrat", sans-serif;
  }
  .stage {
    position: relative; width: 1200px; height: 900px;
    display: flex; flex-direction: column; align-items: center; justify-content: center; gap: 40px;
  }
  .card {
    width: 700px; height: 400px; position: relative;
    box-shadow: 0 10px 30px rgba(0,0,0,.45);
  }
  .card--back {
    background: var(--brand-blue);
    display: flex; align-items: center; justify-content: center; gap: 18px;
  }
  .back-wordmark {
    color: var(--paper); font-weight: 700; font-size: 52px; letter-spacing: 1px;
  }
  .back-dot { width: 22px; height: 22px; border-radius: 50%; background: var(--paper); }
  .card--front { background: var(--paper); display: flex; align-items: center; }
  .front-brand {
    width: 380px; display: flex; align-items: center; justify-content: center; gap: 14px;
  }
  .front-wordmark { color: var(--ink); font-weight: 700; font-size: 64px; letter-spacing: 1px; }
  .front-dot { width: 20px; height: 20px; border-radius: 50%; background: var(--brand-blue); }
  .divider { width: 1px; height: 200px; background: var(--rule); }
  .contact { padding-left: 34px; }
  .contact__name { color: var(--brand-green); font-weight: 700; font-size: 26px; }
  .contact__role { color: var(--ink); font-size: 17px; margin-top: 2px; }
  .contact__company { color: var(--brand-blue); font-size: 17px; font-weight: 500; }
  .contact__list { list-style: none; margin-top: 22px; }
  .contact__item {
    display: flex; align-items: center; gap: 12px;
    color: var(--ink); font-size: 15px; line-height: 26px;
  }
  .contact__icon { width: 14px; height: 14px; flex: none; }
</style>
</head>
<body>
<main class="stage">
  <section class="card card--back" aria-label="Card back">
    <span class="back-dot"></span>
    <span class="back-wordmark">Nectra</span>
  </section>

  <section class="card card--front" aria-label="Card front">
    <div class="front-brand">
      <span class="front-dot"></span>
      <span class="front-wordmark">Nectra</span>
    </div>
    <div class="divider"></div>
    <div class="contact">
      <p class="contact__name">Daniel Shaw</p>
      <p class="contact__role">Founder/ CEO</p>
      <p class="contact__company">Nectra.One</p>
      <ul class="contact__list">
        <li class="contact__item">
          <svg class="contact__icon" viewBox="0 0 24 24" aria-hidden="true"><path fill="#537bbf" d="M6.6 10.8a15.1 15.1 0 0 0 6.6 6.6l2.2-2.2c.3-.3.7-.4 1-.2 1.1.4 2.3.6 3.6.6.6 0 1 .4 1 1V20c0 .6-.4 1-1 1A17 17 0 0 1 3 4c0-.6.4-1 1-1h3.5c.6 0 1 .4 1 1 0 1.3.2 2.5.6 3.6.1.3 0 .7-.2 1z"/></svg>
          555-014-2290
        </li>
        <li class="contact__item">
          <svg class="contact__icon" viewBox="0 0 24 24" aria-hidden="true"><rect x="2.5" y="5" width="19" height="14" fill="none" stroke="#537bbf" stroke-width="2"/><path d="M3 6l9 7 9-7" fill="none" stroke="#537bbf" stroke-width="2"/></svg>
          daniel.shaw@nectra.one
        </li>
        <li class="contact__item">
          <svg class="contact__icon" viewBox="0 0 24 24" aria-hidden="true"><g fill="none" stroke="#537bbf" stroke-width="1.8"><circle cx="12" cy="12" r="9.5"/><ellipse cx="12" cy="12" rx="4" ry="9.5"/><path d="M2.5 12h19M4 7h16M4 17h16"/></g></svg>
          www.Nectra.one
        </li>
      </ul>
    </div>
  </section>
</main>
</body>
</html>
```